Marine Services Letterhead design

We need a letterhead design for an Australian owned company in Victoria named K+T Harbour Works Pty Ltd. We provide linesmen and launches to assist the large ships that come into port.
Our colour is orange.
The final design should have a strong nautical theme and communicate safety and reliability.
I would like to use the letter head on invoices so it should print to pdf well.

Target Market(s)

Owners and representatives of shipping companies. It is not for general public

Industry/Entity Type

Nautical

Requirements
Must have
• A shipping theme, not overly complicated, featuring safety orange colours but not all orange of course.
The letterhead should just sit at the top of the page so I can use for invoices.
Nice to have
• Something elegant and stylish
Should not have
• cartoons or pop art

```html
<!DOCTYPE html>
<html lang="en">
<head>
<meta charset="utf-8">
<title>K+T Harbour Works Pty Ltd – Letterhead</title>
<link rel="stylesheet" href="https://fonts.googleapis.com/css2?family=Source+Sans+3:wght@400;600&display=swap">
<style>
  :root {
    --paper: #ffffff;
    --backdrop: #ffffff;
    --orange: #b0692a;
    --ink: #3a3a3a;
    --black: #111111;
    --rule: #9a9a9a;
  }
  html, body {
    margin: 0;
    padding: 0;
    background: var(--backdrop);
    overflow: hidden;
  }
  .letterhead {
    position: relative;
    width: 946px;
    height: 1200px;
    background: var(--paper);
    overflow: hidden;
    font-family: "Source Sans 3", "Myriad Pro", Arial, sans-serif;
  }
  .brand-mark {
    position: absolute;
    left: 43px;
    top: 96px;
    display: flex;
    align-items: center;
    gap: 14px;
  }
  .brand-mark .dot {
    width: 34px;
    height: 34px;
    border-radius: 50%;
    background: var(--orange);
  }
  .brand-mark .name {
    font-size: 26px;
    font-weight: 600;
    color: var(--orange);
    white-space: nowrap;
  }
  .company-block {
    position: absolute;
    left: 616px;
    top: 86px;
    height: 74px;
    border-left: 1px solid var(--rule);
    padding-left: 8px;
  }
  .company-name {
    margin: 4px 0 0;
    font-size: 22px;
    font-weight: 600;
    color: var(--orange);
    line-height: 1.2;
  }
  .company-address {
    margin: 8px 0 0;
    font-size: 17px;
    color: var(--ink);
    display: flex;
    align-items: center;
    gap: 6px;
  }
  .company-address svg { width: 12px; height: 17px; }
  .footer-wave {
    position: absolute;
    left: 0;
    top: 0;
    width: 946px;
    height: 1200px;
  }
  .footer-details {
    position: absolute;
    right: 44px;
    top: 1106px;
    text-align: right;
    color: #ffffff;
    font-size: 19px;
    line-height: 1;
  }
  .footer-details p { margin: 0 0 24px; }
  .footer-details .phone {
    display: inline-flex;
    align-items: center;
    gap: 4px;
  }
  .footer-details .phone svg { width: 18px; height: 18px; }
</style>
</head>
<body>
  <main class="letterhead">
    <div class="brand-mark">
      <span class="dot"></span>
      <span class="name">K+T Harbour Works</span>
    </div>

    <header class="company-block">
      <h1 class="company-name">K+T Harbour Works Pty Ltd</h1>
      <p class="company-address">
        <svg viewBox="0 0 12 17" aria-hidden="true"><path d="M6 0C2.7 0 0 2.6 0 5.8 0 10 6 17 6 17s6-7 6-11.2C12 2.6 9.3 0 6 0zm0 8.2A2.3 2.3 0 1 1 6 3.6a2.3 2.3 0 0 1 0 4.6z" fill="var(--orange)"/></svg>
        PO Box 214 Seacliff Bay 3941
      </p>
    </header>

    <svg class="footer-wave" viewBox="0 0 946 1200" aria-hidden="true">
      <path d="M0,1022 C60,1090 130,1138 205,1156 C130,1128 60,1088 0,1048 Z" fill="var(--black)"/>
      <path d="M670,1108 C780,1060 870,1030 946,1020 L946,1045 C860,1055 770,1080 670,1108 Z" fill="var(--black)"/>
      <path d="M0,1048 C120,1140 260,1172 400,1168 C590,1160 760,1080 946,1048 L946,1200 L0,1200 Z" fill="var(--orange)"/>
    </svg>

    <footer class="footer-details">
      <p class="phone">
        <svg viewBox="0 0 20 20" aria-hidden="true"><circle cx="10" cy="10" r="9" fill="none" stroke="#fff" stroke-width="1.5"/><path d="M7.2 5.5l1.6 2.4-1 1.1c.6 1.3 1.5 2.2 2.8 2.8l1.1-1 2.4 1.6-.8 1.7c-3.8-.4-7.2-3.8-7.6-7.6z" fill="#fff"/></svg>
        1300 000 418
      </p>
      <p class="abn">ABN: 48203915662</p>
    </footer>
  </main>
</body>
</html>
```